New Interrior Decoration company needs new website

We need a website for our new company specialising in interior decoration to residential and commercial markets.
We supply and install decorative and printed films for office and home decoration such as feature walls.
We would like to keep the design simple and clean.

Target Market(s)

Architects and interior designaers

Industry/Entity Type

It Company

Number of Pages Required

5+ page

Font styles to use
Sans Serif

Requirements
Must have
• Home page,
• Services/products page (split into commercial and residential)
• Gallery (split into commercial and residential)
• contact form and page
Nice to have
• Very clean and minimalistic design.

```html
<!DOCTYPE html>
<html lang="en">
<head>
<meta charset="utf-8">
<title>Vantage Interiors — Home &amp; Commercial Interior</title>
<link rel="stylesheet" href="https://fonts.googleapis.com/css2?family=Cinzel:wght@400&family=Raleway:wght@400;500;600;700&family=Open+Sans:ital,wght@0,400;1,400&display=swap">
<style>
:root{
  --white:#ffffff;
  --ink:#222222;
  --muted:#6f6f6f;
  --about-bg:#f2f2f2;
  --blue-top:#0a7fd6;
  --blue-bottom:#0436a0;
  --testimonial-bg:#ececec;
  --footer-bg:#333333;
  --footer-text:#bdbdbd;
  --quote:#5a5a5a;
}
*{box-sizing:border-box;margin:0;padding:0}
html,body{width:1200px;height:2198px;overflow:hidden;background:var(--white)}
body{position:relative;font-family:"Raleway",Arial,sans-serif;color:var(--ink)}
.abs{position:absolute}

/* hero */
.hero{left:0;top:0;width:1200px;height:577px;
  background:linear-gradient(180deg,#5e5a55 0%,#8a8580 40%,#b9b3aa 70%,#6a6158 100%)}
.hero-shade{left:0;top:0;width:1200px;height:577px;background:linear-gradient(180deg,rgba(0,0,0,.35),rgba(0,0,0,.05) 40%,rgba(0,0,0,.15))}
.brand{left:125px;top:44px;display:flex;align-items:center;gap:10px;color:var(--white);font-weight:700;font-size:30px;letter-spacing:.5px}
.brand-mark{width:40px;height:40px;background:#1c5fbf}
.main-nav{left:517px;top:60px;display:flex;gap:0}
.main-nav a{color:var(--white);text-decoration:none;font-size:15px;font-weight:500;margin-right:43px;padding-bottom:12px}
.main-nav a.active{border-bottom:2px solid var(--white)}
.hero-title{left:0;width:1200px;top:262px;text-align:center;color:var(--white);font-family:"Cinzel",Georgia,serif;text-shadow:0 2px 6px rgba(0,0,0,.4)}
.hero-title h1{font-size:50px;font-weight:400;line-height:1}
.hero-title p{font-size:34px;line-height:1.1;margin-top:6px}
.dots{left:562px;top:532px;display:flex;gap:6px}
.dots span{width:18px;height:18px;border-radius:50%;background:var(--white)}
.dots span.current{background:transparent;border:2px solid var(--white)}

/* about */
.about{left:0;top:577px;width:598px;height:409px;background:var(--about-bg);text-align:center}
.about h2{margin-top:90px;font-size:25px;font-weight:500;letter-spacing:.3px}
.about .lead{margin:18px auto 0;width:420px;font-family:"Open Sans",Arial,sans-serif;font-size:14px;line-height:23px;color:var(--muted)}
.about .body{margin:14px auto 0;width:420px;font-family:"Open Sans",Arial,sans-serif;font-size:12.5px;line-height:25px;color:var(--muted)}
.btn{display:inline-block;margin-top:20px;width:128px;height:40px;border:2px solid #555;font-size:13px;font-weight:600;line-height:36px;color:var(--ink)}
.about-photo{left:598px;top:577px;width:602px;height:409px;
  background:radial-gradient(ellipse at 50% 30%,#8c4a5c 0%,#5e2a3a 55%,#3c1a24 100%)}
.about-photo::after{content:"";position:absolute;left:0;right:0;bottom:0;height:150px;background:linear-gradient(180deg,rgba(230,220,205,0),#d8d2c8)}

/* services */
.services{left:0;top:986px;width:1200px;height:440px;background:linear-gradient(180deg,var(--blue-top),var(--blue-bottom))}
.rule{top:62px;height:1px;background:rgba(255,255,255,.45)}
.section-tag{left:505px;top:39px;width:183px;height:47px;border:1px solid rgba(255,255,255,.7);color:var(--white);font-size:18px;font-weight:600;text-align:center;line-height:45px}
.service{top:121px;width:300px;text-align:center;color:var(--white)}
.service svg{display:block;margin:0 auto}
.service h3{margin-top:24px;font-size:21px;font-weight:500}
.service p{margin-top:6px;font-family:"Open Sans",Arial,sans-serif;font-size:13.5px;line-height:21px;color:rgba(255,255,255,.8)}
.curve{left:0;top:1330px}

/* gallery */
.gallery-title{left:0;top:1398px;width:1200px;text-align:center;font-size:25px;font-weight:500}
.tile{top:1447px;width:229px;height:179px}
.tile-1{left:129px;background:linear-gradient(160deg,#8a7a52,#4f4a3e 60%,#2d2c2a)}
.tile-2{left:366px;background:linear-gradient(180deg,#77806e,#6b7163 60%,#b9b2a3)}
.tile-3{left:604px;background:linear-gradient(160deg,#9c9c98,#b89a6e 60%,#5a4a38)}
.tile-4{left:842px;background:linear-gradient(160deg,#c8d47a,#e7ecd0 50%,#d9dcd2)}
.tile-overlay{position:absolute;inset:4px;border:1px solid rgba(255,255,255,.8);background:rgba(40,40,40,.35);color:var(--white);text-align:center;padding-top:70px}
.tile-overlay strong{display:block;font-size:16px;font-weight:600}
.tile-overlay span{display:block;margin-top:6px;font-family:"Open Sans",Arial,sans-serif;font-size:12.5px;color:rgba(255,255,255,.8)}

/* testimonials */
.testimonials{left:0;top:1692px;width:1200px;height:315px;background:var(--testimonial-bg);text-align:center}
.testimonials h2{margin-top:52px;font-size:23px;font-weight:500}
.quote-text{margin:24px auto 0;width:720px;font-family:"Open Sans",Arial,sans-serif;font-style:italic;font-size:17px;line-height:30px;color:var(--quote)}
.qmark{top:1778px;font-family:Georgia,serif;font-size:80px;line-height:1;color:var(--quote);font-weight:700}
.avatar{left:487px;top:1906px;width:58px;height:58px;border-radius:50%;background:radial-gradient(circle,#e0a070,#b0603a);border:2px solid #fff}
.author{left:558px;top:1917px;text-align:left}
.author strong{display:block;font-size:16px;font-weight:500}
.author span{display:block;margin-top:4px;font-size:10.5px;color:var(--muted)}

/* footer */
.footer{left:0;top:2007px;width:1200px;height:191px;background:var(--footer-bg);text-align:center}
.footer-nav{margin-top:45px;display:flex;justify-content:center;gap:43px}
.footer-nav a{color:var(--white);text-decoration:none;font-size:15px;font-weight:500}
.copyright{margin-top:18px;font-family:"Open Sans",Arial,sans-serif;font-size:12px;color:var(--footer-text)}
.social{margin-top:24px;display:flex;justify-content:center;gap:11px}
.social span{width:36px;height:36px;border-radius:50%;background:var(--white)}
</style>
</head>
<body>

<div class="abs hero" role="img" aria-label="Photo of a modern open-plan kitchen and dining area with pendant lamps"></div>
<div class="abs hero-shade"></div>
<div class="abs brand"><span class="brand-mark"></span>VANTAGE INTERIORS</div>
<nav class="abs main-nav">
  <a class="active" href="#">HOME</a><a href="#">SERVICES</a><a href="#">PRODUCTS</a><a href="#">GALLERY</a><a href="#">CONTACT US</a>
</nav>
<div class="abs hero-title">
  <h1>HOME &amp; COMMERCIAL INTERIOR</h1>
  <p>CURABITUR VEL DOLOR ULTRICE</p>
</div>
<div class="abs dots"><span class="current"></span><span></span><span></span><span></span></div>

<section class="abs about">
  <h2>ABOUT VANTAGE INTERIORS</h2>
  <p class="lead">Fusce ultricies orci ac feugiat suscipit leo massa sodales velit et scelerisque mi tortor at ipsum cligula</p>
  <p class="body">augue bibendum accumsan vestibulum ut commodo a mi Morbi ornare gravida elit Integer congue augue et malesuada iaculis ipsum dui aliquet felis at cursus magna nisl nec elit Praesent</p>
  <a class="btn">READ MORE</a>
</section>
<div class="abs about-photo" role="img" aria-label="Photo of a cream sectional sofa in front of a burgundy feature wall"></div>

<section class="abs services">
  <div class="abs rule" style="left:205px;width:300px"></div>
  <div class="abs rule" style="left:688px;width:310px"></div>
  <div class="abs section-tag">OUR SERVICES</div>

  <div class="abs service" style="left:146px">
    <svg width="112" height="124" viewBox="0 0 112 124" fill="none" stroke="#fff" stroke-width="1.5">
      <path d="M1 1H111V84H66L56 96L46 84H1Z" stroke-opacity=".6"/>
      <g stroke-width="3"><path d="M50 22h12v10H50z"/><path d="M56 32v10M46 42h20l-6 12 6 12H46l6-12z"/></g>
    </svg>
    <h3>Interior decoration</h3>
    <p>Class aptent taciti sociosqu ad litora<br>torquent conubia nim</p>
  </div>
  <div class="abs service" style="left:461px">
    <svg width="112" height="124" viewBox="0 0 112 124" fill="none" stroke="#fff" stroke-width="1.5">
      <path d="M1 1H111V84H66L56 96L46 84H1Z" stroke-opacity=".6"/>
      <g stroke-width="3"><path d="M26 36h60M32 36v32M80 36v32M26 22v46M86 22v46M26 52h60M44 52v16M68 52v16"/></g>
    </svg>
    <h3>Residential Service</h3>
    <p>Class aptent taciti sociosqu ad litora<br>torquent conubia nim</p>
  </div>
  <div class="abs service" style="left:768px">
    <svg width="112" height="124" viewBox="0 0 112 124" fill="none" stroke="#fff" stroke-width="1.5">
      <path d="M1 1H111V84H66L56 96L46 84H1Z" stroke-opacity=".6"/>
      <g stroke-width="3"><path d="M34 18h44v50H34zM40 24h32v36H40zM40 24l10 18M72 24l-10 18M50 62h12"/></g>
    </svg>
    <h3>Commercial Service</h3>
    <p>Class aptent taciti sociosqu ad litora<br>torquent conubia nim</p>
  </div>
</section>
<svg class="abs curve" width="1200" height="100" viewBox="0 0 1200 100"><path d="M0 91Q600 -50 1200 91V100H0Z" fill="#fff"/></svg>

<h2 class="abs gallery-title">OUR GALLERY</h2>
<div class="abs tile tile-1" role="img" aria-label="Photo of a retail interior with lit shelving">
  <div class="tile-overlay"><strong>PROJECT NAME</strong><span>Cum sociis natoque penatibu</span></div>
</div>
<div class="abs tile tile-2" role="img" aria-label="Photo of a sideboard against a green-grey wall with a pendant lamp"></div>
<div class="abs tile tile-3" role="img" aria-label="Photo of a commercial lobby with a curved wooden counter"></div>
<div class="abs tile tile-4" role="img" aria-label="Photo of a bright living room with a lime printed feature wall"></div>

<section class="abs testimonials">
  <h2>TESTIMONIALS</h2>
  <p class="quote-text">Praesent elementum elit at tellus nec ultricies sit amet porttitor mattis enim In massa libero interdum nec interdum vel blandit sed nulla In ullamcorper est eget tempor cursus neque mi consectetuer mi a ultricies massa est sed nisl Class aptent</p>
</section>
<div class="abs qmark" style="left:172px">&ldquo;</div>
<div class="abs qmark" style="left:964px">&rdquo;</div>
<div class="abs avatar" role="img" aria-label="Author portrait"></div>
<div class="abs author"><strong>BY AUTHOR NAME</strong><span>CITY LOCATION</span></div>

<footer class="abs footer">
  <nav class="footer-nav"><a href="#">HOME</a><a href="#">SERVICES</a><a href="#">PRODUCTS</a><a href="#">GALLERY</a><a href="#">CONTACT US</a></nav>
  <p class="copyright">© 2016 Company Name &nbsp;All right reserved &nbsp;Term of Use</p>
  <div class="social" aria-label="Social links"><span></span><span></span><span></span><span></span></div>
</footer>

</body>
</html>
```